business card for a massage therapy practice named 'Cedar and Willow Massage Studio'

I really need a trendy, yet easy on the eyes business card to complement my logo. Ideally with some gold or rose gold foil work.

My uploaded file of the logo I have in horizontal but I have a vertical version as well. Another color that is used in the website is a blush pink here and there. I'd like to see some trendy tropical leaves in the design.

```html
<!DOCTYPE html>
<html lang="en">
<head>
<meta charset="utf-8">
<title>Cedar and Willow Massage Studio – Business Card</title>
<link href="https://fonts.googleapis.com/css2?family=Open+Sans:wght@400;600&display=swap" rel="stylesheet">
<style>
  :root {
    --page-bg: #e9e8e6;
    --card-white: #ffffff;
    --card-dark: #545558;
    --ink: #3b3b3b;
    --ink-soft: #6a6a6a;
    --rule: #d8d8d8;
    --mint: #6fd3b5;
    --gold: #b59c5e;
    --list-text: #e6e6e6;
  }
  * { box-sizing: border-box; margin: 0; padding: 0; }
  html, body {
    width: 1200px; height: 844px; overflow: hidden;
    background: var(--page-bg);
    font-family: "Open Sans", Arial, sans-serif;
  }
  .stage { position: relative; width: 1200px; height: 844px; }

  .card {
    position: absolute; top: 272px;
    width: 520px; height: 300px;
    box-shadow: 0 6px 18px rgba(0,0,0,.18);
    overflow: hidden;
  }

  /* Front */
  .card-front { left: 50px; background: var(--card-white); }
  .brand {
    position: absolute; top: 46px; right: 40px;
    display: flex; align-items: center; gap: 14px;
  }
  .brand-mark { width: 40px; height: 40px; border-radius: 50%; background: var(--gold); }
  .brand-name {
    font-weight: 600; font-size: 22px; line-height: 1.15;
    color: var(--ink); letter-spacing: .2px;
  }
  .rule {
    position: absolute; left: 40px; right: 40px; height: 1px; background: var(--rule);
  }
  .rule-top { top: 122px; }
  .rule-bottom { top: 152px; }
  .contact { position: absolute; left: 40px; bottom: 34px; color: var(--ink); }
  .person-name {
    font-size: 17px; font-weight: 400; color: var(--mint);
    letter-spacing: .6px; text-transform: uppercase;
  }
  .person-role { font-size: 14px; margin-bottom: 10px; }
  .address { font-size: 14px; margin-bottom: 6px; }
  .lines { font-size: 14px; }
  .label { color: var(--mint); font-weight: 600; }
  .divider { color: var(--ink-soft); margin: 0 8px; }

  /* Back */
  .card-back { left: 630px; background: var(--card-dark); }
  .services {
    position: absolute; left: 28px; top: 104px; list-style: none;
  }
  .services li {
    font-size: 11.5px; color: var(--list-text);
    letter-spacing: .4px; text-transform: uppercase;
    line-height: 19px; padding-left: 13px; position: relative;
  }
  .services li::before {
    content: ""; position: absolute; left: 0; top: 7px;
    width: 6px; height: 6px; border-radius: 50%; background: var(--mint);
  }
  .photo {
    position: absolute; right: 0; top: 0; width: 240px; height: 300px;
    background: linear-gradient(160deg, #6a6a6e 0%, #c9a793 38%, #e2c2b0 55%, #b9b9bb 80%, #a8a8aa 100%);
  }
</style>
</head>
<body>
<main class="stage">
  <section class="card card-front" aria-label="Business card front">
    <div class="brand">
      <span class="brand-mark"></span>
      <span class="brand-name">Cedar &amp; Willow<br>Massage Studio</span>
    </div>
    <div class="rule rule-top"></div>
    <div class="rule rule-bottom"></div>
    <div class="contact">
      <p class="person-name">Marisol Vega</p>
      <p class="person-role">Massage Therapist</p>
      <p class="address">2418 Alder St. suite 210 Sacramento, CA 95816</p>
      <p class="lines"><span class="label">P:</span> (916) 555-0148<span class="divider">|</span><span class="label">E:</span> hello@cedarandwillow.com</p>
    </div>
  </section>

  <section class="card card-back" aria-label="Business card back">
    <ul class="services">
      <li>Clinical Bodywork</li>
      <li>Therapeutic Massage</li>
      <li>Integrated Hot Stone Massage</li>
      <li>Lymphatic Drainage Massage</li>
      <li>Sacramento Sinus Facial</li>
      <li>Australian Foot Treatment</li>
    </ul>
    <div class="photo" role="img" aria-label="Photo of a therapist's hands massaging a client's neck and shoulders"></div>
  </section>
</main>
</body>
</html>
```